Business Card for Lantern Reach

Please design a Modern Business card for a Online Marketing Company

Website: http://www.lanternreach-example.com.au

Please do NOT include physical address in design.

```html
<!DOCTYPE html>
<html lang="en">
<head>
<meta charset="utf-8">
<title>Lantern Reach – Business Card</title>
<link rel="stylesheet" href="https://fonts.googleapis.com/css2?family=Roboto:wght@400;700;900&family=Questrial&display=swap">
<style>
  :root {
    --backdrop: #d6d6d6;
    --card: #ffffff;
    --brand-red: #c8283c;
    --brand-red-dark: #a81c2f;
    --brand-gold: #e8b524;
    --brand-orange: #eea43a;
    --ink: #2b2b2b;
    --ink-soft: #555555;
  }
  * { box-sizing: border-box; margin: 0; padding: 0; }
  html, body {
    width: 1200px; height: 871px; overflow: hidden;
    background: var(--backdrop);
  }
  .canvas { position: relative; width: 1200px; height: 871px; }

  .card {
    position: absolute; width: 560px; height: 320px;
    background: var(--card);
    box-shadow: 0 14px 30px rgba(0,0,0,0.22);
    overflow: hidden;
  }
  .card--front { left: 110px; top: 80px; }
  .card--back  { left: 530px; top: 470px; }

  .brand { display: flex; flex-direction: column; align-items: center; }
  .brand__row { display: flex; align-items: center; gap: 10px; white-space: nowrap; }
  .brand__square { background: var(--brand-red); flex: none; }
  .brand__name {
    font-family: "Roboto", sans-serif; font-weight: 900;
    color: var(--brand-red); text-transform: uppercase; letter-spacing: 0.5px;
  }
  .brand__tagline {
    font-family: "Roboto", sans-serif; font-weight: 700; color: var(--ink);
    white-space: nowrap;
  }

  .card--front .brand {
    position: absolute; left: 0; right: 0; top: 122px;
  }
  .card--front .brand__square { width: 30px; height: 30px; }
  .card--front .brand__name { font-size: 34px; }
  .card--front .brand__tagline { font-size: 15px; margin-top: 4px; }

  .card--back .brand {
    position: absolute; left: 30px; top: 112px; width: 230px;
  }
  .card--back .brand__square { width: 18px; height: 18px; }
  .card--back .brand__name { font-size: 20px; }
  .card--back .brand__tagline { font-size: 10px; margin-top: 3px; }

  .contact {
    position: absolute; left: 300px; top: 118px;
    font-family: "Questrial", sans-serif;
  }
  .contact__name {
    font-family: "Roboto", sans-serif; font-weight: 700;
    font-size: 17px; color: var(--brand-gold); letter-spacing: 0.4px;
    white-space: nowrap;
  }
  .contact__role { font-size: 13px; color: var(--brand-red); margin-bottom: 12px; }
  .contact__list { list-style: none; }
  .contact__item {
    display: flex; align-items: center; gap: 12px;
    font-size: 13px; color: var(--ink-soft); line-height: 24px;
    white-space: nowrap;
  }
  .contact__icon { width: 13px; height: 13px; flex: none; }

  .card__bands { position: absolute; left: 0; bottom: 0; width: 560px; height: 40px; }
</style>
</head>
<body>
<main class="canvas">

  <section class="card card--front" aria-label="Business card front">
    <div class="brand">
      <div class="brand__row">
        <span class="brand__square"></span>
        <span class="brand__name">Lantern Reach</span>
      </div>
      <span class="brand__tagline">Be seen online - Grow online</span>
    </div>
  </section>

  <section class="card card--back" aria-label="Business card back">
    <div class="brand">
      <div class="brand__row">
        <span class="brand__square"></span>
        <span class="brand__name">Lantern Reach</span>
      </div>
      <span class="brand__tagline">Be seen online - Grow online</span>
    </div>

    <div class="contact">
      <p class="contact__name">Marcus D. Whitfield</p>
      <p class="contact__role">CEO</p>
      <ul class="contact__list">
        <li class="contact__item">
          <svg class="contact__icon" viewBox="0 0 16 16"><path fill="var(--brand-orange)" d="M3.5 1l2.6 3-1.4 1.8c.9 2 2.5 3.6 4.5 4.5L11 8.9l3 2.6-1.5 2.6C7 14 2 9 1.9 3.4z"/></svg>
          <span>555-014-2297</span>
        </li>
        <li class="contact__item">
          <svg class="contact__icon" viewBox="0 0 16 16"><rect x="1" y="3" width="14" height="10" fill="var(--brand-orange)"/><path d="M1.5 3.5L8 9l6.5-5.5" fill="none" stroke="#fff" stroke-width="1.4"/></svg>
          <span>mwhitfield@example-mail.com</span>
        </li>
        <li class="contact__item">
          <svg class="contact__icon" viewBox="0 0 16 16"><circle cx="8" cy="8" r="6.5" fill="none" stroke="var(--brand-orange)" stroke-width="1.6"/><circle cx="8" cy="8" r="2.4" fill="var(--brand-orange)"/></svg>
          <span>www.lanternreach-example.com.au</span>
        </li>
      </ul>
    </div>

    <svg class="card__bands" viewBox="0 0 560 40" preserveAspectRatio="none" aria-hidden="true">
      <polygon points="0,28 300,28 300,40 0,40" fill="var(--brand-gold)"/>
      <polygon points="280,40 300,24 560,24 560,40" fill="var(--brand-red)"/>
      <polygon points="300,24 560,24 560,28 305,28" fill="var(--brand-red-dark)"/>
    </svg>
  </section>

</main>
</body>
</html>
```